Business Card Design for company

We want new business cards. We'd like something different-- yet still highly professional. Our tagline is Providing leadership, delivering success. Stock photos are ok, as long as they are relevant and look upscale.

Target Market(s)

Architecture/Business Management Consulting/Engineering Consulting

Contact Information for Business Card

dark gray background with pops of blue might be good, but you tell me. You're the designers. Rounded corners might be nice, but again, you tell me.

Font styles to use
Serif
Sans Serif

Colors
3276b5
5c5c5c
9d9d9d
fbfbfb

Requirements
Nice to have
• Something different, but still very professional.

```html
<!DOCTYPE html>
<html lang="en">
<head>
<meta charset="UTF-8">
<title>Halvern Global – Business Cards</title>
<link rel="stylesheet" href="https://fonts.googleapis.com/css2?family=Montserrat:wght@400;500;700&family=Work+Sans:wght@400;500&display=swap">
<style>
  :root {
    --blue: #3276b5;
    --blue-deep: #1f5fa6;
    --blue-light: #3f86c8;
    --ink: #5c5c5c;
    --mid: #9d9d9d;
    --paper: #fbfbfb;
    --backdrop: #262626;
  }
  * { box-sizing: border-box; margin: 0; padding: 0; }
  html, body { width: 1200px; height: 900px; overflow: hidden; }
  body {
    background: var(--backdrop);
    display: flex;
    align-items: center;
    justify-content: center;
    gap: 40px;
    font-family: "Work Sans", sans-serif;
  }
  .card {
    position: relative;
    width: 540px;
    height: 309px;
    border-radius: 26px;
    overflow: hidden;
    background: linear-gradient(160deg, var(--blue-light) 0%, var(--blue) 45%, var(--blue-deep) 100%);
    color: var(--paper);
  }

  /* Front */
  .card-front__map {
    position: absolute;
    inset: 20px 30px 20px 30px;
    border-radius: 50%;
    background: radial-gradient(ellipse at 55% 45%, rgba(120,180,235,0.32) 0%, rgba(80,150,220,0.12) 55%, rgba(50,118,181,0) 75%);
  }
  .card-front__brand {
    position: absolute;
    left: 0; right: 0; top: 78px;
    text-align: center;
    font-family: "Montserrat", sans-serif;
    font-weight: 500;
    color: var(--paper);
    line-height: 1;
  }
  .brand-word--main { display: block; font-size: 62px; letter-spacing: 2px; }
  .brand-word--sub { display: block; font-size: 26px; letter-spacing: 5px; margin-top: 8px; }
  .card-front__tagline {
    position: absolute;
    left: 0; right: 0; bottom: 58px;
    text-align: center;
    font-size: 13px;
    letter-spacing: 2px;
    text-transform: uppercase;
    color: var(--paper);
  }

  /* Back */
  .card-back__band {
    position: absolute;
    left: 0; right: 0; bottom: 0;
    height: 68px;
    background: var(--paper);
  }
  .card-back__rule {
    position: absolute;
    left: 0; right: 0; bottom: 73px;
    height: 2px;
    background: var(--paper);
  }
  .card-back__address {
    position: absolute;
    left: 0; right: 0; bottom: 24px;
    text-align: center;
    font-size: 12.5px;
    color: var(--blue);
  }
  .card-back__brand {
    position: absolute;
    left: 34px; top: 56px;
    width: 230px;
    text-align: center;
    font-family: "Montserrat", sans-serif;
    font-weight: 500;
    line-height: 1;
  }
  .card-back__brand .brand-word--main { font-size: 44px; }
  .card-back__brand .brand-word--sub { font-size: 18px; letter-spacing: 4px; margin-top: 6px; }
  .card-back__divider {
    position: absolute;
    left: 290px; top: 36px;
    width: 1px; height: 140px;
    background: rgba(251,251,251,0.7);
  }
  .card-back__contact {
    position: absolute;
    left: 310px; top: 44px;
  }
  .contact-name {
    font-family: "Montserrat", sans-serif;
    font-weight: 700;
    font-size: 17px;
    letter-spacing: 1px;
    text-transform: uppercase;
  }
  .contact-role { font-size: 12px; font-weight: 500; margin: 3px 0 10px; }
  .contact-list { list-style: none; font-size: 11.5px; line-height: 17px; }
  .contact-list li { display: flex; align-items: center; gap: 7px; }
  .contact-icon { width: 10px; height: 10px; flex: none; }
</style>
</head>
<body>

  <section class="card card-front" aria-label="Business card front">
    <div class="card-front__map" role="img" aria-label="Faint dotted world map in light blue"></div>
    <div class="card-front__brand">
      <span class="brand-word--main">HALVERN</span>
      <span class="brand-word--sub">GLOBAL</span>
    </div>
    <p class="card-front__tagline">Guiding Strategy | Building Lasting Results</p>
  </section>

  <section class="card card-back" aria-label="Business card back">
    <div class="card-back__brand">
      <span class="brand-word--main">HALVERN</span>
      <span class="brand-word--sub">GLOBAL</span>
    </div>
    <div class="card-back__divider"></div>
    <div class="card-back__contact">
      <p class="contact-name">Daniel Ashby</p>
      <p class="contact-role">Design Consultant</p>
      <ul class="contact-list">
        <li>
          <svg class="contact-icon" viewBox="0 0 10 10"><rect x="2.5" y="0.5" width="5" height="9" rx="1" fill="none" stroke="currentColor"/></svg>
          555-014-2290
        </li>
        <li>
          <svg class="contact-icon" viewBox="0 0 10 10"><path d="M2 1 L4 1 L4.6 3 L3.4 4 Q4.5 6 6 6.6 L7 5.4 L9 6 L9 8 Q5 9 2.5 6 Q1 4 2 1Z" fill="currentColor"/></svg>
          01632 960418 (Redbury)
        </li>
        <li>
          <svg class="contact-icon" viewBox="0 0 10 10"><path d="M2 1 L4 1 L4.6 3 L3.4 4 Q4.5 6 6 6.6 L7 5.4 L9 6 L9 8 Q5 9 2.5 6 Q1 4 2 1Z" fill="currentColor"/></svg>
          01632 960733 (Oakfield)
        </li>
        <li>
          <svg class="contact-icon" viewBox="0 0 10 10"><rect x="0.5" y="2" width="9" height="6" fill="none" stroke="currentColor"/><path d="M0.5 2 L5 5.5 L9.5 2" fill="none" stroke="currentColor"/></svg>
          info@HalvernGlobal
        </li>
        <li>
          <svg class="contact-icon" viewBox="0 0 10 10"><circle cx="5" cy="5" r="4.3" fill="none" stroke="currentColor"/><ellipse cx="5" cy="5" rx="1.8" ry="4.3" fill="none" stroke="currentColor"/><line x1="0.7" y1="5" x2="9.3" y2="5" stroke="currentColor"/></svg>
          www.HalvernGlobal.com
        </li>
      </ul>
    </div>
    <div class="card-back__rule"></div>
    <div class="card-back__band"></div>
    <p class="card-back__address">Unit 8, The Marlow Centre, Elm Park, Redbury, Herts RB4 2QN</p>
  </section>

</body>
</html>
```